Defense Attorney Business Card Design Project/ Stationary

I am looking for a distinctive business card design for my solo law practice.
I practice criminal defense, both juvenile and adult, including DUI. I am a very experienced attorney with prior military experience. The design should convey a traditional, old school flair, but not be too stodgy or uptight. Some color. My logo should appear.
Updates

Project Deadline Extended Reason: I misunderstood how this project works and I was not prepared with my logo when this project ran the first time. Added Thursday, November 13, 2014

Project Deadline Extended
Reason: I was sent overseas on military duty last year, which interrupted this project. Thank you for your participation... I hope we can get this done this week! Thank you, Neil

Target Market(s)

Regular everyday people looking for strong, knowledgeable, authoritative representation while they are faced with criminal charges. Many have never been charged with a crime before. A reassuring air is therefore desired.

Industry/Entity Type

Business

Contact Information for Business Card

My information is:
Theodore M. Quill, Attorney at Law
785 Birch Avenue Suite 300
Oakland, California 94719
Tel: (510) 384-6125
Fax: (510) 391-7802
email: neilquilllaw@mailvine.example
web: www.neilquilllaw.example

Font styles to use
Serif
Sans Serif
Decorative

Colors
0255a3
ffffff

Requirements
Must have
• Sharp lines, bold elements. Conservative use of colors, such as deep blues, burgundy, grays for example.
• While my logo says "Neil Quill", it should be modified to show "Theodore M. Quill".
Should not have
• Cliche imagery such as scales of justice, gavels, Statue of Liberty, etc.

```html
<!DOCTYPE html>
<html lang="en">
<head>
<meta charset="utf-8">
<title>Neil Quill – Business Cards</title>
<link rel="stylesheet" href="https://fonts.googleapis.com/css2?family=Cinzel:wght@400;500&family=Raleway:wght@300;400&display=swap">
<style>
  :root {
    --backdrop: #f1f1f0;
    --card-light: #ffffff;
    --card-dark: #2a2827;
    --ink-navy: #2b3550;
    --ink-cream: #d9d1b6;
    --shadow: rgba(0,0,0,0.12);
  }
  * { margin: 0; padding: 0; box-sizing: border-box; }
  html, body {
    width: 1200px; height: 696px; overflow: hidden;
    background: var(--backdrop);
  }
  .stage { position: relative; width: 1200px; height: 696px; }

  .card {
    position: absolute;
    box-shadow: 0 6px 18px var(--shadow);
  }

  /* Front: contact details (portrait) */
  .card--contact {
    left: 130px; top: 68px;
    width: 320px; height: 560px;
    background: var(--card-light);
    color: var(--ink-navy);
    padding: 40px 38px;
  }
  .brand-name {
    font-family: "Cinzel", serif;
    font-weight: 500;
    letter-spacing: 0.04em;
  }
  .card--contact .brand-name {
    text-align: center;
    font-size: 22px;
    color: var(--ink-navy);
    margin-bottom: 34px;
  }
  .rule {
    width: 26px; height: 2px;
    background: var(--ink-navy);
    margin-bottom: 14px;
  }
  .block { margin-bottom: 26px; }
  .person-name {
    font-family: "Cinzel", serif;
    font-size: 15px;
    letter-spacing: 0.05em;
    margin-bottom: 4px;
  }
  .person-title, .contact-list {
    font-family: "Raleway", sans-serif;
    font-weight: 300;
    font-size: 12.5px;
  }
  .contact-list { list-style: none; line-height: 1.55; }
  .address {
    font-family: "Cinzel", serif;
    font-size: 13.5px;
    line-height: 1.5;
    letter-spacing: 0.03em;
    font-style: normal;
  }

  /* Back: brand (landscape) */
  .card--brand {
    left: 560px; top: 210px;
    width: 560px; height: 320px;
    background: var(--card-dark);
    color: var(--ink-cream);
  }
  .card--brand .brand-name {
    position: absolute;
    left: 0; right: 0; top: 108px;
    text-align: center;
    font-size: 40px;
    color: var(--ink-cream);
  }
  .card--brand .rule {
    position: absolute;
    left: 180px; top: 226px;
    width: 28px; height: 2px;
    background: var(--ink-cream);
  }
  .card--brand .web {
    position: absolute;
    left: 180px; top: 246px;
    font-family: "Raleway", sans-serif;
    font-weight: 400;
    font-size: 15px;
    letter-spacing: 0.02em;
  }
</style>
</head>
<body>
<main class="stage">
  <section class="card card--contact">
    <div class="brand-name">Neil Quill</div>

    <div class="rule"></div>
    <div class="block">
      <div class="person-name">THEODORE M. QUILL</div>
      <div class="person-title">Attorney at Law (Criminal Defense)</div>
    </div>

    <div class="rule"></div>
    <ul class="block contact-list">
      <li>T: (510) 384-6125</li>
      <li>F: (510) 391-7802</li>
      <li>E: neilquilllaw@mailvine.example</li>
      <li>W: www.neilquilllaw.example</li>
    </ul>

    <div class="rule"></div>
    <address class="address">
      785 Birch Avenue, Suite 300<br>
      Oakland, California 94719
    </address>
  </section>

  <section class="card card--brand">
    <div class="brand-name">Neil Quill</div>
    <div class="rule"></div>
    <div class="web">neilquilllaw.example</div>
  </section>
</main>
</body>
</html>
```